Personal training and nutrition business needs business card design

We need a business card that outlays our services and invites potential customers to join our team and take the first step to a healthier and more enjoyable life. We cater for any level of fitness and specialize in weight loss and conditioning, strength training, muscle gain and strength endurance. Whether you are just starting off or need some help getting to the next level of your journey we are here to get the job done.
We specialize in one on one or one on two personal training sessions and each program will be custom made to suit individual fitness goals of our clients

```html
<!DOCTYPE html>
<html lang="en">
<head>
<meta charset="utf-8">
<title>Stride &amp; Tempo – Business Card</title>
<link rel="stylesheet" href="https://fonts.googleapis.com/css2?family=Exo+2:ital,wght@0,800;1,800&family=Oswald:wght@500&family=Roboto:wght@400&display=swap">
<style>
  :root{
    --backdrop:#2a2a2a;
    --paper:#ededed;
    --paper-edge:#dcdcdc;
    --ink:#151515;
    --body:#2c2c2c;
    --plum:#a0579a;
    --violet:#5d3a8a;
    --rim:#4b3790;
    --white:#ffffff;
  }
  *{margin:0;padding:0;box-sizing:border-box}
  html,body{width:1200px;height:1138px;overflow:hidden;background:var(--backdrop)}
  .canvas{position:relative;width:1200px;height:1138px}
  .card{position:absolute;width:620px;height:375px;border-radius:16px;overflow:hidden;
    background:linear-gradient(180deg,#f3f3f3,var(--paper) 60%,var(--paper-edge));
    box-shadow:0 6px 14px rgba(0,0,0,.45)}
  .card--front{left:274px;top:186px}
  .card--back{left:276px;top:608px}

  /* front */
  .brand{position:absolute;display:flex;align-items:center;gap:14px}
  .brand__dot{width:30px;height:30px;border-radius:50%;background:var(--plum)}
  .brand__name{font-family:"Exo 2",sans-serif;font-weight:800;letter-spacing:1px;color:var(--ink)}
  .card--front .brand{left:0;right:0;top:178px;justify-content:center}
  .card--front .brand__name{font-size:40px}
  .tagline{font-family:"Oswald",sans-serif;font-weight:500;letter-spacing:1.3px;text-transform:uppercase}
  .card--front .tagline{position:absolute;top:252px;left:0;right:0;text-align:center;font-size:14px;color:var(--plum)}
  .web-row{position:absolute;top:320px;left:0;right:0;display:flex;justify-content:center;align-items:center;gap:18px;
    font-family:"Roboto",sans-serif;font-size:16px;color:var(--ink)}
  .web-row__rule{width:70px;height:2px;background:var(--ink);border-radius:2px}
  .accent{color:var(--plum)}
  .accent-deep{color:var(--violet)}
  .front-band{position:absolute;left:0;right:0;bottom:0;height:9px;background:linear-gradient(90deg,var(--plum),var(--violet))}

  /* back */
  .back-panel{position:absolute;left:0;top:0}
  .card--back .brand{left:52px;top:196px;flex-direction:column;align-items:flex-start;gap:0}
  .card--back .brand__name{font-size:33px;line-height:36px}
  .card--back .brand__dot{position:absolute;left:100px;top:-90px;width:56px;height:56px;background:var(--white)}
  .card--back .tagline{position:absolute;left:52px;top:278px;font-size:9.5px;color:var(--white)}
  .contact{position:absolute;left:344px;top:88px;font-family:"Roboto",sans-serif;color:var(--body)}
  .contact__name{font-family:"Exo 2",sans-serif;font-style:italic;font-weight:800;font-size:24px;letter-spacing:.5px;
    background:linear-gradient(90deg,var(--violet),var(--plum));-webkit-background-clip:text;background-clip:text;color:transparent}
  .contact__role{font-size:16px;margin-top:2px}
  .contact__list{list-style:none;margin-top:26px}
  .contact__item{display:flex;align-items:center;gap:18px;font-size:16px;height:24.5px}
  .contact__item svg{width:14px;height:14px;fill:var(--violet)}
  .contact__address{margin-top:12px;font-size:16px;line-height:24px}
</style>
</head>
<body>
<main class="canvas">

  <section class="card card--front" aria-label="Card front">
    <div class="brand">
      <span class="brand__dot"></span>
      <span class="brand__name">STRIDE &amp; TEMPO</span>
    </div>
    <p class="tagline">Personal training.&nbsp; Nutrition. Motivation</p>
    <div class="web-row">
      <span class="web-row__rule"></span>
      <span>www.<span class="accent">stride</span>and<span class="accent-deep">tempo</span>.com</span>
      <span class="web-row__rule"></span>
    </div>
    <div class="front-band"></div>
  </section>

  <section class="card card--back" aria-label="Card back">
    <svg class="back-panel" width="620" height="375" viewBox="0 0 620 375" aria-hidden="true">
      <defs>
        <linearGradient id="panelFill" x1="0.6" y1="0" x2="0.2" y2="1">
          <stop offset="0" stop-color="#a2599b"/>
          <stop offset="1" stop-color="#5c3a88"/>
        </linearGradient>
      </defs>
      <path d="M0 0 H243 Q367 190 263 375 H0 Z" fill="var(--rim)"/>
      <path d="M0 0 H236 Q360 190 256 375 H0 Z" fill="url(#panelFill)"/>
    </svg>

    <div class="brand">
      <span class="brand__dot"></span>
      <span class="brand__name">STRIDE &amp;</span>
      <span class="brand__name">TEMPO</span>
    </div>
    <p class="tagline">Personal training.&nbsp; Nutrition. Motivation</p>

    <div class="contact">
      <h1 class="contact__name">MARK DALTON</h1>
      <p class="contact__role">Personal Trainer</p>
      <ul class="contact__list">
        <li class="contact__item">
          <svg viewBox="0 0 16 16" aria-label="Phone"><path d="M3 2h3l1 3-2 1a8 8 0 0 0 5 5l1-2 3 1v3a1 1 0 0 1-1 1A13 13 0 0 1 2 3a1 1 0 0 1 1-1z"/></svg>
          <span>+1 (555) 214-7380</span>
        </li>
        <li class="contact__item">
          <svg viewBox="0 0 16 16" aria-label="Email"><path d="M1 3h14v10H1z M2 4l6 5 6-5" fill="var(--violet)" stroke="#ededed" stroke-width="1.2"/></svg>
          <span>mark@strideandtempo.com</span>
        </li>
        <li class="contact__item">
          <svg viewBox="0 0 16 16" aria-label="Website"><circle cx="8" cy="8" r="6.5" fill="none" stroke="var(--violet)" stroke-width="1.3"/><path d="M1.5 8h13M8 1.5c-3 3-3 10 0 13M8 1.5c3 3 3 10 0 13" fill="none" stroke="var(--violet)" stroke-width="1.1"/></svg>
          <span>www.<span class="accent-deep">stride</span>and<span class="accent">tempo</span>.com</span>
        </li>
      </ul>
      <p class="contact__address">1820 Maple Ridge Lane<br>Fairview Ohio 44120</p>
    </div>
  </section>

</main>
</body>
</html>
```